Design material for Lumora Event

We need a design of POSM for Lumora Event
1. Content:
- The Lumora Event 3rd
- Singapore 28.10.2018
- A placeholder for insert logo of sponsors (limit 10 logo)
2. POSM:
- Backdrop: 5,5m and 2,6m
- Banner: 4m and 0,5m
- Standee: 0,8m and 2m
- Cover: A4 size
3. Style:
We need style simply because we are a hospital.
Main color: light blue and a little of green (if can)

Hope to see your design soon!

Font styles to use
Sans Serif

Colors
0792cd
85cae6
86cfc6
33b8a4
33a6d7

```html
<!DOCTYPE html>
<html lang="en">
<head>
<meta charset="utf-8">
<title>Lumora Event — Cover</title>
<link href="https://fonts.googleapis.com/css2?family=Montserrat:wght@200;300;400;600;700&display=swap" rel="stylesheet">
<style>
  :root {
    --navy-blue: #0d5f88;
    --sky-blue: #33a6d7;
    --teal: #33b8a4;
    --mint: #86cfc6;
    --sage: #8cc5a4;
    --text-grey: #8a8a8a;
    --rule: #cfe5d2;
    --paper: #ffffff;
  }
  * { margin: 0; padding: 0; box-sizing: border-box; }
  html, body { width: 848px; height: 1200px; overflow: hidden; background: var(--paper); }
  .cover {
    position: relative; width: 848px; height: 1200px; overflow: hidden;
    font-family: "Montserrat", sans-serif; background: var(--paper);
  }
  .pattern-backdrop {
    position: absolute; left: 0; top: 0; width: 848px; height: 600px;
    background: linear-gradient(180deg, #e6e6e6 0%, #efefef 45%, #ffffff 100%);
  }
  .edition {
    position: absolute; left: 395px; top: 188px; font-weight: 700; font-size: 124px;
    line-height: 1; color: var(--sage);
  }
  .edition sup { font-size: 26px; font-weight: 300; vertical-align: top; position: relative; top: 36px; left: 2px; }
  .title-light {
    position: absolute; left: 0; width: 848px; top: 302px; text-align: center;
    font-weight: 200; font-size: 70px; color: var(--navy-blue); letter-spacing: 1px; line-height: 1;
  }
  .title-bold {
    position: absolute; left: 0; width: 848px; top: 363px; text-align: center;
    font-weight: 700; font-size: 100px; color: var(--navy-blue); line-height: 1; letter-spacing: 2px;
  }
  .city {
    position: absolute; left: 0; width: 848px; top: 473px; text-align: center;
    font-weight: 600; font-size: 17px; letter-spacing: 8px; color: var(--teal); padding-left: 8px;
  }
  .date { position: absolute; left: 315px; top: 492px; width: 220px; height: 60px; }
  .date .day { position: absolute; left: 0; top: 0; font-weight: 300; font-size: 31px; color: var(--sky-blue); line-height: 1; }
  .date .month { position: absolute; left: 0; top: 32px; font-weight: 700; font-size: 20px; letter-spacing: 1.5px; color: var(--teal); line-height: 1; }
  .date .number { position: absolute; left: 133px; top: -6px; font-weight: 300; font-size: 66px; color: var(--sky-blue); line-height: 1; }
  .year {
    position: absolute; left: 0; width: 848px; top: 560px; text-align: center;
    font-weight: 300; font-size: 20px; letter-spacing: 40px; padding-left: 40px; color: var(--navy-blue);
  }
  .rule { position: absolute; left: 208px; top: 604px; width: 426px; height: 2px; background: var(--rule); }
  .intro {
    position: absolute; left: 210px; top: 625px; width: 428px;
    font-weight: 300; font-size: 13.6px; line-height: 17.2px; color: var(--text-grey); text-align: justify;
  }
  .skyline-photo {
    position: absolute; left: 0; top: 800px; width: 848px; height: 400px;
    background: linear-gradient(180deg, #ffffff 0%, #eef1ef 18%, #c7cfcb 45%, #8f9c96 72%, #6f8079 86%, #8fa39a 100%);
  }
  .sponsors {
    position: absolute; left: 68px; top: 786px; width: 710px; height: 40px;
    display: flex; align-items: center; justify-content: space-between;
  }
  .sponsor {
    display: flex; align-items: center; gap: 4px;
    font-weight: 700; font-size: 9.5px; color: #2e3a40; text-transform: uppercase; white-space: nowrap;
  }
  .sponsor .dot { width: 9px; height: 9px; border-radius: 50%; background: var(--sky-blue); }
  .sponsor .square { width: 9px; height: 9px; background: var(--teal); }
  .email {
    position: absolute; left: 0; width: 848px; top: 866px; text-align: center;
    font-weight: 600; font-size: 14px; color: var(--text-grey);
  }
</style>
</head>
<body>
<main class="cover">
  <div class="pattern-backdrop" role="img" aria-label="Soft grey geometric diamond pattern background"></div>

  <div class="edition">3<sup>rd</sup></div>
  <h1 class="title-light">LUMORA</h1>
  <div class="title-bold">EVENT</div>

  <div class="city">SINGAPORE</div>
  <div class="date">
    <span class="day">SUNDAY</span>
    <span class="month">OCTOBER</span>
    <span class="number">28</span>
  </div>
  <div class="year">2018</div>

  <div class="rule"></div>
  <p class="intro">At vero eos et accusamus et iusto odio dignissimos ducimus qui blanditiis praesentium voluptatum deleniti atque corrupti quos dolores et quas molestias excepturi sint occaecati cupiditate non provident, similique sunt in culpa qui officia deserunt mollitia animi, id est laborum et dolorum fuga.</p>

  <div class="skyline-photo" role="img" aria-label="Photograph of the Singapore waterfront skyline with towers, a lotus-shaped museum and a helix bridge"></div>

  <ul class="sponsors" aria-label="Sponsors">
    <li class="sponsor"><span class="dot"></span>Bluecrest</li>
    <li class="sponsor">Oakline</li>
    <li class="sponsor"><span class="square"></span>Fernhill</li>
    <li class="sponsor">Velto</li>
    <li class="sponsor">Harbor Co</li>
    <li class="sponsor">Northvale Guild</li>
    <li class="sponsor"><span class="square"></span>tidewise</li>
    <li class="sponsor">Carrowmore</li>
    <li class="sponsor">Kestrel Paddle</li>
    <li class="sponsor"><span class="dot"></span>Sixpoint</li>
  </ul>

  <div class="email">LumoraEvent@email.com</div>
</main>
</body>
</html>
```